Garlic Farm for Farm Sales/Restaurant sales

Need a professional, but appealing to agriculture world. We are selling 27 kinds of Organic Garlic from a farm in Simla,CO. I have uploaded logo and business information-we are going to need a template, because I will need to use it for four separate people.
-We are trying to appeal to Farm to table restaurants
-As well as growers/farmers

Target Market(s)

Agriculture Sales/Restaurants-Organic

Industry/Entity Type

Agriculture

Contact Information for Business Card

Want it to look more unique then your average kelto stock card- I want it to look amazing

Font styles to use
Sans Serif

Colors
0455a3
ec1f27
fbed22
ffffff

Requirements
Must have
• Just be creative
Nice to have
• Colorful
Should not have
• plain

```html
<!DOCTYPE html>
<html lang="en">
<head>
<meta charset="utf-8">
<title>Plains Ridge Garlic – Business Card</title>
<link rel="stylesheet" href="https://fonts.googleapis.com/css2?family=Open+Sans:wght@400;600;700&display=swap">
<style>
  :root {
    --navy: #0b2f5f;
    --red: #bc0a2a;
    --yellow: #fbd800;
    --white: #ffffff;
    --backdrop: #ecebe8;
  }
  * { margin: 0; padding: 0; box-sizing: border-box; }
  html, body { width: 1200px; height: 900px; overflow: hidden; }
  body {
    position: relative;
    background: var(--backdrop);
    font-family: "Open Sans", Arial, sans-serif;
    color: var(--white);
  }
  .card {
    position: absolute;
    background: var(--navy);
    overflow: hidden;
    box-shadow: 0 6px 18px rgba(0,0,0,0.18);
  }

  /* Front card */
  .card-front { left: 78px; top: 34px; width: 588px; height: 364px; }
  .front-band {
    position: absolute; left: 0; top: 59px; width: 100%; height: 247px;
    background: var(--red);
  }
  .contact-block { position: absolute; left: 30px; top: 70px; }
  .person-name { font-size: 22px; font-weight: 700; line-height: 1.2; }
  .person-title { font-size: 16px; font-weight: 400; line-height: 1.2; }
  .address { margin-top: 38px; font-size: 16px; line-height: 18px; }
  .contact-list { list-style: none; margin-top: 20px; }
  .contact-list li {
    display: flex; align-items: center; gap: 9px;
    font-size: 16px; height: 24.5px;
  }
  .contact-list svg { width: 13px; height: 13px; fill: var(--white); flex: none; }
  .garlic-art {
    position: absolute; left: 357px; top: 56px; width: 226px; height: 260px;
    background: radial-gradient(ellipse at 50% 60%, #ffe12a 0%, var(--yellow) 60%, #e9c400 100%);
    border-radius: 50% 50% 46% 46% / 62% 62% 38% 38%;
    box-shadow: 4px 4px 8px rgba(0,0,0,0.35);
  }

  /* Back card */
  .card-back { left: 388px; top: 505px; width: 567px; height: 352px; }
  .back-band {
    position: absolute; left: 0; top: 98px; width: 100%; height: 149px;
    background: var(--yellow);
    display: flex; align-items: center; justify-content: center; gap: 16px;
  }
  .brand-dot {
    width: 86px; height: 86px; border-radius: 50%;
    background: var(--red);
  }
  .brand-name {
    font-size: 40px; font-weight: 700; color: var(--navy);
    letter-spacing: 0.5px;
  }
</style>
</head>
<body>

  <section class="card card-front" aria-label="Business card front">
    <div class="front-band"></div>
    <div class="contact-block">
      <h1 class="person-name">Daniel Corwen</h1>
      <p class="person-title">Managing Director</p>
      <p class="address">12345, Address Goes Here<br>Country Name, 123456</p>
      <ul class="contact-list">
        <li>
          <svg viewBox="0 0 16 16" aria-hidden="true"><path d="M3.5 1.5l2.5 0 1.2 3.2-1.6 1.2c.8 1.8 2.3 3.3 4.1 4.1l1.2-1.6 3.2 1.2v2.5c0 .8-.7 1.4-1.5 1.4C6.9 13.5 2.5 9.1 2.1 3 2.1 2.2 2.7 1.5 3.5 1.5z"/></svg>
          (719)-555-0142
        </li>
        <li>
          <svg viewBox="0 0 16 16" aria-hidden="true"><path d="M4 1h7v4H4zM2 5h12v9H2zm3 3v2h2V8zm4 0v2h2V8zm-4 3v2h2v-2zm4 0v2h2v-2z"/></svg>
          719-555-0187
        </li>
        <li>
          <svg viewBox="0 0 16 16" aria-hidden="true"><path d="M1 3h14v10H1zm1.5 1.2V5l5.5 3.8L13.5 5v-.8L8 7.9z"/></svg>
          hello@plainsridge.com
        </li>
        <li>
          <svg viewBox="0 0 16 16" aria-hidden="true"><circle cx="8" cy="8" r="7"/></svg>
          www.plainsridge.com
        </li>
      </ul>
    </div>
    <div class="garlic-art" role="img" aria-label="Illustration of a yellow garlic bulb"></div>
  </section>

  <section class="card card-back" aria-label="Business card back">
    <div class="back-band">
      <span class="brand-dot" aria-hidden="true"></span>
      <span class="brand-name">Plains Ridge Garlic</span>
    </div>
  </section>

</body>
</html>
```